National Sales - Pick Up Truck Dealer

We need a logo design for a new vehicle dealership based in Sydney, Norvania. The business name is Coastal Iron Haulers Motor Co. We will be selling American 'trucks/pick up trucks' like KRV, Torvan, Blaxer, Morrow T420, Kenzo Raptors, Morrow T640 and the likes.

These vehicles are a luxury option and we would like the logo to be strong, luxurious and masculine.Colours will be black and red or black and blue with the option of grey and white.

Target Market(s)

Men

Industry/Entity Type

Car Dealer

Contact Information for Business Card

Dennis Harlowe
Managing Director
0412 639 274
den@qelvtrk.com.au

Level 5, Brindle Parkway
17 Pemberly Lane
Kestrel Downs
KDR
Norvania
Licence No: MD493152

Back of the card

qelvtrk.com.au

Font styles to use
Sans Serif

Colors

Designer to choose colors to be used in the design.

Requirements
Must have
• The company logo that is in the attachments, you can choose from the three which one you would like to work with. Must have vehicle images ....Please look at the attachments as they show examples of what we like and also provides potential images. If you choose to put an image on the front even if it is just the front of the vehicle can you please use the Black KRV Sorrento. Must have all details from the business card details section front and back
Nice to have
• N/A
Should not have
• No cars or standard trucks, please refer to the attached images to understand the product . Should not have any new logos or branding. No other colours besides what is in the logo you choose.

```html
<!DOCTYPE html>
<html lang="en">
<head>
<meta charset="utf-8">
<title>Coastal Iron Haulers Motor Co – Business Card</title>
<link href="https://fonts.googleapis.com/css2?family=Open+Sans:wght@400;600;700&display=swap" rel="stylesheet">
<style>
  :root {
    --stage: #2b2623;
    --card-black: #0d0d0d;
    --red: #e4232b;
    --red-dark: #7e1418;
    --red-deep: #3a0508;
    --white: #ffffff;
    --grey: #c9c9c9;
  }
  * { box-sizing: border-box; margin: 0; padding: 0; }
  html, body {
    width: 1200px; height: 716px; overflow: hidden;
    background: var(--stage);
    font-family: "Open Sans", Arial, sans-serif;
  }
  .canvas { position: relative; width: 1200px; height: 716px; }
  .card {
    position: absolute; top: 205px;
    width: 500px; height: 305px;
    overflow: hidden;
    box-shadow: 0 14px 30px rgba(0,0,0,.45);
  }
  /* Front */
  .card--front { left: 70px; }
  .front-photo {
    position: absolute; inset: 0;
    background:
      radial-gradient(ellipse at 70% 35%, rgba(255,60,60,.55), transparent 45%),
      linear-gradient(160deg, var(--red-deep) 0%, var(--red-dark) 45%, #b3171d 75%, var(--red-deep) 100%);
  }
  .front-name {
    position: absolute; left: 0; right: 0; top: 125px;
    text-align: center;
    color: var(--white); font-weight: 700; font-size: 24px; letter-spacing: .5px;
    line-height: 1.15;
  }
  /* Back */
  .card--back { left: 630px; background: var(--card-black); }
  .back-band {
    position: absolute; left: 0; right: 0; bottom: 0; height: 128px;
    background: linear-gradient(100deg, var(--red) 0%, #c91c23 35%, var(--red) 55%, var(--red-dark) 80%, var(--red) 100%);
  }
  .person { position: absolute; left: 26px; top: 130px; }
  .person__name { color: var(--red); font-weight: 700; font-size: 20px; line-height: 1.1; }
  .person__role { color: var(--white); font-weight: 700; font-size: 10px; margin-top: 2px; }
  .contacts { position: absolute; left: 26px; top: 196px; list-style: none; }
  .contacts li {
    display: flex; align-items: center; gap: 8px;
    color: var(--white); font-size: 11px; line-height: 17px;
  }
  .contacts svg { width: 10px; height: 10px; flex: none; }
  .brand { position: absolute; right: 26px; top: 62px; width: 220px; text-align: right; }
  .brand__name { color: var(--white); font-weight: 700; font-size: 19px; line-height: 1.15; }
  .brand__licence { color: var(--grey); font-size: 11px; margin-top: 10px; }
  .address {
    position: absolute; right: 26px; bottom: 22px;
    text-align: right; color: var(--white); font-size: 11.5px; line-height: 16px;
    font-style: normal;
  }
</style>
</head>
<body>
<main class="canvas">
  <section class="card card--front">
    <div class="front-photo" role="img" aria-label="Red-toned photo of a Black KRV Sorrento pickup truck in an urban street"></div>
    <div class="front-name">Coastal Iron Haulers<br>Motor Co</div>
  </section>

  <section class="card card--back">
    <div class="back-band"></div>
    <div class="person">
      <div class="person__name">Dennis Harlowe</div>
      <div class="person__role">Managing Director</div>
    </div>
    <ul class="contacts">
      <li>
        <svg viewBox="0 0 10 10"><rect x="2.5" y="0.5" width="5" height="9" rx="1" fill="none" stroke="#fff" stroke-width="1"/></svg>
        0412 639 274
      </li>
      <li>
        <svg viewBox="0 0 10 10"><rect x="0.5" y="2" width="9" height="6" fill="none" stroke="#fff" stroke-width="1"/><path d="M0.5 2 L5 5.5 L9.5 2" fill="none" stroke="#fff" stroke-width="1"/></svg>
        den@qelvtrk.com.au
      </li>
      <li>
        <svg viewBox="0 0 10 10"><circle cx="5" cy="5" r="4.3" fill="none" stroke="#fff" stroke-width="1"/><path d="M0.7 5 H9.3 M5 0.7 C2.5 3 2.5 7 5 9.3 M5 0.7 C7.5 3 7.5 7 5 9.3" fill="none" stroke="#fff" stroke-width=".8"/></svg>
        www.qelvtrk.com.au
      </li>
    </ul>
    <div class="brand">
      <div class="brand__name">Coastal Iron Haulers<br>Motor Co</div>
      <div class="brand__licence">Licence No: MD493152</div>
    </div>
    <address class="address">
      Level 5, Brindle Parkway,<br>
      17 Pemberly Lane,<br>
      Kestrel Downs, KDR, Norvania
    </address>
  </section>
</main>
</body>
</html>
```